Wendmoor Vapes labels

We need a label designed for our e-liquid that we will be selling from our store. (E-liquid is used in electronic cigarettes) The label should be 1-1.5 inches tall and ~3 inches long.

Try to focus on highlighting the name brand over the specific flavor.

Bottle size will be 15ml clear bottles.

There will be 10+ flavors and each flavor will need a slightly different label (with the same overall theme) and different nicotine levels varying from 0mg, 6mg, 12mg, and 18mg.

Initial favor list is:
Copper Lagoon
Velvet Slurp
Zesty Figs
Tumble Plums
Guava Riot
Fizzy Gems
Amber Falcon
Frostleaf
Glowstone
Marlo
Maple Twirl

Please add the following warning in caps and small font:

(WHITE FONT)
This product contains nicotine or was produced at a facility that processes nicotine which has been known to cause birth defects and other reproductive harm. This product also contains VG/PG and artificial flavors. Not for sale to minors.
(RED FONT)
Toxic if swallowed or has contact with skin. Keep locked up and out of reach of children and pets. In case of accident or you feel unwell seek medical advice immediately.

Target Market(s)

young adults

Industry/Entity Type

Electronic

```html
<!DOCTYPE html>
<html lang="en">
<head>
<meta charset="utf-8">
<title>Wendmoor Vapes – e-liquid labels</title>
<link href="https://fonts.googleapis.com/css2?family=Oswald:wght@300;400;600&display=swap" rel="stylesheet">
<style>
  :root {
    --page: #ffffff;
    --teal: #2fbfae;
    --teal-deep: #17a394;
    --teal-stripe: #1a9e8e;
    --black-label: #070809;
    --green-label: #116b5e;
    --white-label: #ffffff;
    --warn-white: #ffffff;
    --warn-red: #e8322f;
    --warn-dark: #1a1a1a;
    --brand-blue: #2f6fc0;
    --brand-grey: #9aa3ab;
  }
  * { margin: 0; padding: 0; box-sizing: border-box; }
  html, body { width: 1000px; height: 1200px; overflow: hidden; background: var(--page); }
  body { position: relative; font-family: "Oswald", "Arial Narrow", sans-serif; }

  .label {
    position: absolute;
    left: 161px;
    width: 678px;
    height: 338px;
    background: var(--label-bg);
    overflow: hidden;
  }
  .label--black { top: 57px;  --label-bg: var(--black-label); --right-warn: var(--warn-white); --art-a: #1d7a68; --art-b: #14574b; }
  .label--green { top: 436px; --label-bg: var(--green-label); --right-warn: var(--warn-white); --art-a: #22c2b0; --art-b: #169c8d; }
  .label--white { top: 815px; --label-bg: var(--white-label); --right-warn: var(--warn-dark); --art-a: #2cc4b2; --art-b: #18a896; border: 1px solid #333; }

  .warning {
    position: absolute;
    top: 10px;
    height: 318px;
    writing-mode: vertical-rl;
    transform: rotate(180deg);
    font-weight: 300;
    font-size: 9.2px;
    line-height: 14.5px;
    letter-spacing: 0.1px;
    text-transform: uppercase;
    text-align: start;
  }
  .warning--toxic    { left: 16px;  width: 60px; color: var(--warn-red); }
  .warning--nicotine { left: 574px; width: 60px; color: var(--right-warn); }

  .nicotine-band {
    position: absolute;
    left: 82px; top: 0;
    width: 42px; height: 100%;
    background: var(--teal);
    display: flex; align-items: center; justify-content: center;
  }
  .nicotine-band span {
    writing-mode: vertical-rl;
    transform: rotate(180deg);
    color: #fff;
    font-weight: 300;
    font-size: 18px;
    margin-bottom: 40px;
  }

  .stripe { position: absolute; top: 0; height: 100%; }
  .stripe--outer { left: 550px; width: 7px; background: var(--teal-stripe); }
  .stripe--inner { left: 557px; width: 9px; background: var(--teal); }

  .brand {
    position: absolute;
    left: 226px; top: 14px;
    display: flex; align-items: center; gap: 12px;
  }
  .brand-dot { width: 50px; height: 50px; border-radius: 50%; background: var(--brand-grey); }
  .brand-name {
    color: var(--brand-blue);
    font-weight: 600;
    font-size: 27px;
    line-height: 1;
    text-transform: uppercase;
    letter-spacing: 1px;
  }
  .brand-name small { display: block; font-size: 14px; letter-spacing: 9px; margin-top: 4px; text-align: center; }

  .flavour-art { position: absolute; left: 258px; top: 96px; }

  .ribbon { position: absolute; left: 216px; top: 268px; }
  .ribbon-name {
    position: absolute;
    left: 216px; top: 275px;
    width: 224px;
    text-align: center;
    color: #fff;
    font-weight: 300;
    font-size: 20px;
    line-height: 30px;
    text-transform: uppercase;
  }
</style>
</head>
<body>

<section class="label label--black">
  <p class="warning warning--toxic">Toxic if swallowed or has contact with skin. Keep locked up and out of reach of children and pets. In case of accident or you feel unwell seek medical advice immediately.</p>
  <div class="nicotine-band"><span>Nicotine by volume: 0mg/mL</span></div>
  <div class="brand"><div class="brand-dot"></div><div class="brand-name">Wendmoor<small>Vapes</small></div></div>
  <svg class="flavour-art" width="142" height="180" role="img" aria-label="Large drop emblem decoration">
    <defs><linearGradient id="art-black" x1="0" y1="0" x2="0" y2="1"><stop offset="0" stop-color="var(--art-a)"/><stop offset="1" stop-color="var(--art-b)"/></linearGradient></defs>
    <rect x="0" y="0" width="142" height="180" rx="28" fill="url(#art-black)"/>
  </svg>
  <svg class="ribbon" width="226" height="44" viewBox="0 0 226 44"><polygon points="0,10 24,10 24,40 0,40 10,25" fill="var(--teal-deep)"/><polygon points="226,10 202,10 202,40 226,40 216,25" fill="var(--teal-deep)"/><polygon points="14,4 212,4 212,36 14,36" fill="var(--teal)"/></svg>
  <div class="ribbon-name">Copper Lagoon</div>
  <div class="stripe stripe--outer"></div><div class="stripe stripe--inner"></div>
  <p class="warning warning--nicotine">This product contains nicotine or was produced at a facility that processes nicotine which has been known to cause birth defects and other reproductive harm. This product also contains VG/PG and artificial flavors. Not for sale to minors.</p>
</section>

<section class="label label--green">
  <p class="warning warning--toxic">Toxic if swallowed or has contact with skin. Keep locked up and out of reach of children and pets. In case of accident or you feel unwell seek medical advice immediately.</p>
  <div class="nicotine-band"><span>Nicotine by volume: 0mg/mL</span></div>
  <div class="brand"><div class="brand-dot"></div><div class="brand-name">Wendmoor<small>Vapes</small></div></div>
  <svg class="flavour-art" width="142" height="180" role="img" aria-label="Large drop emblem decoration">
    <defs><linearGradient id="art-green" x1="0" y1="0" x2="0" y2="1"><stop offset="0" stop-color="var(--art-a)"/><stop offset="1" stop-color="var(--art-b)"/></linearGradient></defs>
    <rect x="0" y="0" width="142" height="180" rx="28" fill="url(#art-green)"/>
  </svg>
  <svg class="ribbon" width="226" height="44" viewBox="0 0 226 44"><polygon points="0,10 24,10 24,40 0,40 10,25" fill="var(--teal-deep)"/><polygon points="226,10 202,10 202,40 226,40 216,25" fill="var(--teal-deep)"/><polygon points="14,4 212,4 212,36 14,36" fill="var(--teal)"/></svg>
  <div class="ribbon-name">Velvet Slurp</div>
  <div class="stripe stripe--outer"></div><div class="stripe stripe--inner"></div>
  <p class="warning warning--nicotine">This product contains nicotine or was produced at a facility that processes nicotine which has been known to cause birth defects and other reproductive harm. This product also contains VG/PG and artificial flavors. Not for sale to minors.</p>
</section>

<section class="label label--white">
  <p class="warning warning--toxic">Toxic if swallowed or has contact with skin. Keep locked up and out of reach of children and pets. In case of accident or you feel unwell seek medical advice immediately.</p>
  <div class="nicotine-band"><span>Nicotine by volume: 0mg/mL</span></div>
  <div class="brand"><div class="brand-dot"></div><div class="brand-name">Wendmoor<small>Vapes</small></div></div>
  <svg class="flavour-art" width="142" height="180" role="img" aria-label="Large drop emblem decoration">
    <defs><linearGradient id="art-white" x1="0" y1="0" x2="0" y2="1"><stop offset="0" stop-color="var(--art-a)"/><stop offset="1" stop-color="var(--art-b)"/></linearGradient></defs>
    <rect x="0" y="0" width="142" height="180" rx="28" fill="url(#art-white)"/>
  </svg>
  <svg class="ribbon" width="226" height="44" viewBox="0 0 226 44"><polygon points="0,10 24,10 24,40 0,40 10,25" fill="var(--teal-deep)"/><polygon points="226,10 202,10 202,40 226,40 216,25" fill="var(--teal-deep)"/><polygon points="14,4 212,4 212,36 14,36" fill="var(--teal)"/></svg>
  <div class="ribbon-name">Velvet Slurp</div>
  <div class="stripe stripe--outer"></div><div class="stripe stripe--inner"></div>
  <p class="warning warning--nicotine">This product contains nicotine or was produced at a facility that processes nicotine which has been known to cause birth defects and other reproductive harm. This product also contains VG/PG and artificial flavors. Not for sale to minors.</p>
</section>

</body>
</html>
```